Profesional personal website needs design and business card

I need a business card with my professional name as a logo "Dorian Vitality" for my business. I am a Wellness Coach, consultant and trainer. So it should be professional, wellness oriented and modern.

Target Market(s)

Private clients, governments, corporations. Luxury and high market.

Industry/Entity Type

Health And Wellness

Contact Information for Business Card

Dorian Vitality should be the logo

Colors

Designer to choose colors to be used in the design.

Requirements
Must have
• Dorian Vitality
• Name: Tomás Lirandel
• Wellness Coach, Consultant & Trainer.
• Website: www.dorianvitality-example.com
• Phone:
• Spain (+34) 612 480 317
• (USA) +1 (555) 610 4829
Nice to have
• The most important is the design of "Dorian Vitality", as this is going to be my personal brand logo. It should be professional, wellness, high end and actual.
Should not have
• no golds, no baroque style..

```html
<!DOCTYPE html>
<html lang="en">
<head>
<meta charset="utf-8">
<title>Dorian Vitality – Business Card</title>
<link href="https://fonts.googleapis.com/css2?family=Montserrat:wght@400;500;700;800&display=swap" rel="stylesheet">
<style>
  :root {
    --backdrop: #1c1c1e;
    --card-blue: #1a1fa6;
    --accent-yellow: #f7c400;
    --ink-white: #ffffff;
  }
  * { margin: 0; padding: 0; box-sizing: border-box; }
  html, body {
    width: 1200px; height: 900px; overflow: hidden;
    background: var(--backdrop);
    font-family: "Montserrat", sans-serif;
  }
  .stage {
    width: 1200px; height: 900px;
    display: flex; flex-direction: column;
    align-items: center; justify-content: center; gap: 34px;
  }
  .card {
    position: relative;
    width: 700px; height: 400px;
    background: var(--card-blue);
    border-bottom: 8px solid var(--accent-yellow);
    box-shadow: 0 14px 30px rgba(0,0,0,.5);
  }
  .card--front { display: flex; align-items: center; justify-content: center; }
  .wordmark {
    color: var(--ink-white);
    font-weight: 800;
    text-transform: uppercase;
    line-height: 1;
    text-align: left;
  }
  .card--front .wordmark { font-size: 66px; letter-spacing: 2px; }
  .card--back .wordmark { font-size: 44px; letter-spacing: 1px; }
  .wordmark span { display: block; }

  .card--back { display: flex; align-items: center; }
  .back-logo { width: 330px; display: flex; justify-content: center; }
  .divider {
    width: 2px; height: 200px;
    background: var(--accent-yellow);
  }
  .contact { padding-left: 34px; color: var(--ink-white); }
  .contact__name {
    color: var(--accent-yellow);
    font-weight: 700; font-size: 26px; letter-spacing: 1px;
    text-transform: uppercase;
  }
  .contact__role { font-size: 17px; line-height: 1.3; margin: 4px 0 18px; }
  .contact__list { list-style: none; font-size: 17px; }
  .contact__item { display: flex; align-items: center; gap: 10px; height: 28px; }
  .contact__item svg.icon { width: 16px; height: 16px; flex: none; }
  .flag { width: 26px; height: 17px; margin-left: 18px; }
  .highlight { color: var(--accent-yellow); }
</style>
</head>
<body>
<main class="stage">
  <section class="card card--front">
    <div class="wordmark"><span>Dorian</span><span>Vitality</span></div>
  </section>

  <section class="card card--back">
    <div class="back-logo">
      <div class="wordmark"><span>Dorian</span><span>Vitality</span></div>
    </div>
    <div class="divider"></div>
    <div class="contact">
      <h1 class="contact__name">Tomás Lirandel</h1>
      <p class="contact__role">Wellness Coach,<br>Consultant &amp; Trainer</p>
      <ul class="contact__list">
        <li class="contact__item">
          <svg class="icon" viewBox="0 0 16 16"><path d="M4 1l2.5 3-1.5 2c1 2 2.5 3.5 4.5 4.5l2-1.5 3 2.5-1.5 2.5C7 15 1 9 1.5 2.5z" fill="none" stroke="#f7c400" stroke-width="1.4"/></svg>
          (+34) 612 480 317
          <svg class="flag" viewBox="0 0 26 17" role="img" aria-label="Spain"><rect width="26" height="17" fill="#c60b1e"/><rect y="4.25" width="26" height="8.5" fill="#ffc400"/></svg>
        </li>
        <li class="contact__item">
          <svg class="icon" viewBox="0 0 16 16"><rect x="4" y="1" width="8" height="14" rx="1.5" fill="none" stroke="#f7c400" stroke-width="1.4"/><circle cx="8" cy="12.5" r=".9" fill="#f7c400"/></svg>
          +1 (555) 610 4829
          <svg class="flag" viewBox="0 0 26 17" role="img" aria-label="United States"><rect width="26" height="17" fill="#fff"/><g fill="#b22234"><rect y="0" width="26" height="1.9"/><rect y="3.8" width="26" height="1.9"/><rect y="7.6" width="26" height="1.9"/><rect y="11.4" width="26" height="1.9"/><rect y="15.2" width="26" height="1.8"/></g><rect width="11" height="9.5" fill="#3c3b6e"/></svg>
        </li>
        <li class="contact__item">
          <svg class="icon" viewBox="0 0 16 16"><rect x="1.5" y="3.5" width="13" height="9" fill="none" stroke="#f7c400" stroke-width="1.4"/><path d="M1.5 3.5L8 9l6.5-5.5" fill="none" stroke="#f7c400" stroke-width="1.4"/></svg>
          info@dorianvitality-example.com
        </li>
        <li class="contact__item">
          <svg class="icon" viewBox="0 0 16 16"><g fill="none" stroke="#f7c400" stroke-width="1.3"><circle cx="8" cy="8" r="6.5"/><ellipse cx="8" cy="8" rx="3" ry="6.5"/><path d="M1.5 8h13M2.5 4.8h11M2.5 11.2h11"/></g></svg>
          <span>www.<span class="highlight">dorianvitality-example</span>.com</span>
        </li>
      </ul>
    </div>
  </section>
</main>
</body>
</html>
```